IT Freelancer (Consulting, trainer and project manager) needed letterhead

As a freelancer for IT Trainingswhip, consulting and project management I need a letterhead design. What is desired is a design that fits the existing logo (see Annex). It is functional, reliable, and equal time wirkenn Agil and modern. The whole is in color, as well as printed out to make a good impression on a black and white printer. The whole is to the existing Cooperate design (business card, homepage, logo) fit. Therefore, the choice of colors.
Updates

Target Market(s)

Customers such as medium-sized enterprises, training institutions

Industry/Entity Type

Consulting

Colors
0455a3
3277b5
85abd2
cfdfed
34a6d7
32a6d6
249fd4
0792cd
85cae6

Requirements
Must have
• Must include logo (see Annex) address (Brunnerweg 14, 95617 Waldsassen, Germany). Must seriously and act simultaneously Agil. Design should (even) be adaptable (signature, address, etc.) design must look good on a black / white laser

```html
<!DOCTYPE html>
<html lang="en">
<head>
<meta charset="utf-8">
<title>Lukas Brenner – Letterhead</title>
<link rel="stylesheet" href="https://fonts.googleapis.com/css2?family=Lato:wght@400;700;900&display=swap">
<style>
  :root {
    --navy: #0455a3;
    --sky: #34a6d7;
    --mid: #3277b5;
    --ink: #2a2a2a;
    --muted: #555;
    --ghost: #eeeeee;
    --stage: #bdbdbd;
    --paper: #ffffff;
  }
  * { margin: 0; padding: 0; box-sizing: border-box; }
  html, body { width: 1200px; height: 994px; overflow: hidden; }
  body {
    background: var(--stage);
    font-family: "Lato", sans-serif;
    position: relative;
  }
  .letterhead {
    position: absolute;
    left: 267px; top: 27px;
    width: 665px; height: 940px;
    background: var(--paper);
    box-shadow: 0 6px 24px rgba(0,0,0,.18);
    overflow: hidden;
  }
  .corner-bars { position: absolute; left: 0; top: 0; }
  .sender-line {
    position: absolute; left: 70px; top: 118px;
    font-size: 8px; color: var(--muted); letter-spacing: .1px;
  }
  .brand {
    position: absolute; right: 48px; top: 108px;
    display: flex; flex-direction: column; align-items: center; gap: 8px;
  }
  .brand-dot {
    width: 88px; height: 88px; border-radius: 50%;
    background: var(--navy);
  }
  .brand-name {
    font-weight: 900; font-size: 19px; color: var(--navy);
    letter-spacing: 1px; text-align: center; line-height: 1.05;
  }
  .letter-body {
    position: absolute; left: 70px; top: 248px; width: 500px;
    font-size: 11.4px; line-height: 1.45; color: var(--ink);
  }
  .letter-body p { margin-bottom: 12px; }
  .footer-rule {
    position: absolute; left: 0; right: 0; bottom: 96px;
    height: 2px; background: var(--sky);
  }
  .footer-band {
    position: absolute; left: 0; right: 0; bottom: 0; height: 90px;
    background: var(--navy); color: #fff;
    display: flex; flex-direction: column; justify-content: center;
    padding-left: 150px; gap: 6px; font-size: 11.5px;
  }
  .footer-dot {
    position: absolute; left: 40px; bottom: 58px;
    width: 78px; height: 78px; border-radius: 50%;
    background: var(--navy); border: 3px solid #fff;
    box-shadow: 0 0 0 2px var(--sky);
  }
  .contact-row { display: flex; align-items: center; gap: 14px; }
  .contact-item { display: inline-flex; align-items: center; gap: 5px; }
  .contact-item svg { width: 10px; height: 10px; fill: var(--sky); }
</style>
</head>
<body>
  <main class="letterhead">
    <svg class="corner-bars" width="260" height="110" viewBox="0 0 260 110" aria-hidden="true">
      <g fill="var(--ghost)">
        <rect x="40" y="14" width="150" height="10" transform="rotate(-8 40 14)"/>
        <rect x="90" y="36" width="150" height="10" transform="rotate(-8 90 36)"/>
        <rect x="60" y="58" width="150" height="10" transform="rotate(-8 60 58)"/>
        <rect x="110" y="80" width="130" height="10" transform="rotate(-8 110 80)"/>
      </g>
    </svg>

    <div class="sender-line">Lukas Brenner · Brunnerweg 14 · 95617 Steinbach · Germany</div>

    <div class="brand">
      <div class="brand-dot"></div>
      <div class="brand-name">LUKAS<br>BRENNER</div>
    </div>

    <section class="letter-body">
      <p>Lorem ipsum dolor sit amet, consectetur adipiscing elit. Praesent non est diam. Vivamus risus sem, gravida sit amet nibh ut, ornare lobortis ante. Aliquam sollicitudin, mauris tincidunt semper venenatis, orci est pretium augue, ut vestibulum felis velit bibendum urna. Integer sollicitudin aliquet ligula, non ultricies nisl efficitur nec. Aliquam felis lorem, facilisis ac condimentum quis, consectetur volutpat lacus. Proin fermentum sem quis elit efficitur, eu tempus magna maximus.</p>
      <p>Aenean a mi tortor. Morbi pretium mi sed cursus vehicula. Lorem ipsum dolor sit amet, consectetur adipiscing elit. In finibus eros ac maximus finibus. Nunc pretium pellentesque tellus. Nullam accumsan nisl non diam commodo sagittis. Nunc et ante sit amet urna auctor convallis. Maecenas sed fringilla metus, sit amet vulputate felis. Morbi eget tempor nisi. Aliquam erat volutpat. Aenean laoreet interdum tempus.</p>
      <p>Maecenas dignissim placerat mauris, vitae sollicitudin ex. Integer bibendum maximus mauris, ac tempor urna viverra id. Integer tincidunt lobortis nisl at posuere. Sed faucibus vulputate finibus. Maecenas convallis, sem quis pellentesque cursus, urna quam aliquam augue, quis porttitor eros est nec lectus. Sed mattis at tellus ut blandit. Aenean nunc magna, viverra sed mauris vel, porta finibus lacus. Nullam bibendum turpis rutrum porta placerat</p>
      <p>Aenean a mi tortor. Morbi pretium mi sed cursus vehicula. Lorem ipsum dolor sit amet, consectetur adipiscing elit. In finibus eros ac maximus finibus. Nunc pretium pellentesque tellus. Nullam accumsan nisl non diam commodo sagittis. Nunc et ante sit amet urna auctor convallis. Maecenas sed fringilla metus, sit amet vulputate felis. Morbi eget tempor nisi. Aliquam erat volutpat. Aenean laoreet interdum tempus. .</p>
    </section>

    <div class="footer-rule"></div>
    <footer class="footer-band">
      <div class="contact-row"><span class="contact-item">Brunnerweg 14, 95617 Steinbach, Germany</span></div>
      <div class="contact-row">
        <span class="contact-item"><svg viewBox="0 0 10 10"><path d="M2 0.5 L3.6 2.6 L2.8 3.6 Q4 6 6.4 7.2 L7.4 6.4 L9.5 8 L8.3 9.5 Q3.5 9 0.5 1.7 Z"/></svg>512 004 2210</span>
        <span class="contact-item"><svg viewBox="0 0 10 10"><rect x="2" y="0.5" width="6" height="3"/><rect x="0.5" y="3.5" width="9" height="4.5" rx="1"/><rect x="2" y="7" width="6" height="2.5"/></svg>512 004 2211</span>
        <span class="contact-item"><svg viewBox="0 0 10 10"><path d="M0.5 2 H9.5 V8 H0.5 Z M0.5 2 L5 5.5 L9.5 2" stroke="#fff" stroke-width="0.6"/></svg>info@lukasbrenner.de</span>
        <span class="contact-item"><svg viewBox="0 0 10 10"><circle cx="5" cy="5" r="4.5"/></svg>www.lukasbrenner.de</span>
      </div>
    </footer>
    <div class="footer-dot"></div>
  </main>
</body>
</html>
```